Optometrist A5 flyer update 2014

We are an optical / optometrist business needing an existing A5 flyer updated. This flyer has been very successful but needs to be renewed.
We are supplying all the original source files including images.
I have included pdf files with annotations on the alteration we would like made.
We are open to suggestions / alterations to the design of the pamphlet.
We are after a modern design appealing to the various ages of our patient base.

```html
<!DOCTYPE html>
<html lang="en">
<head>
<meta charset="utf-8">
<title>Frequently Asked Questions – Opening Hours</title>
<link rel="stylesheet" href="https://fonts.googleapis.com/css2?family=Ubuntu:wght@400;500;700&display=swap">
<style>
  :root {
    --white: #ffffff;
    --blue-light: #3ea6e2;
    --blue-mid: #2b8fd4;
    --blue-deep: #1c6bb6;
    --ink: #3b3b3b;
    --frame-dark: #2a2a2c;
    --frame-red: #8a2a22;
    --frame-tortoise: #4a2614;
  }
  * { margin: 0; padding: 0; box-sizing: border-box; }
  html, body { width: 846px; height: 1200px; overflow: hidden; background: var(--white); }
  .flyer {
    position: relative;
    width: 846px;
    height: 1200px;
    overflow: hidden;
    font-family: "Ubuntu", sans-serif;
    color: var(--white);
    background: var(--white);
  }
  .backdrop { position: absolute; inset: 0; }
  .product-shot { position: absolute; border-radius: 40px; }
  .shot-wire-black { left: 26px; top: 40px; width: 424px; height: 86px; background: linear-gradient(90deg, #e9e9ea, #cfd0d2, #e9e9ea); }
  .shot-rimless-black { left: 500px; top: 0; width: 346px; height: 160px; background: linear-gradient(90deg, #d7d6d9, #bdbbc0); }
  .shot-red-metal { left: 136px; top: 146px; width: 508px; height: 150px; background: linear-gradient(90deg, #e8d6d3, #c9a29c, #d7d7d7); }
  .shot-tortoise { left: 388px; top: 292px; width: 458px; height: 330px; border-radius: 60px; background: linear-gradient(135deg, #6b3a1e, var(--frame-tortoise) 55%, #2b2b2b); opacity: .9; }
  .question-icon { position: absolute; left: 38px; top: 333px; width: 124px; height: 124px; }
  .faq-title {
    position: absolute; left: 63px; top: 478px;
    font-size: 26px; font-weight: 500; letter-spacing: .1px;
  }
  .faq-list { position: absolute; left: 40px; top: 0; width: 790px; list-style: none; }
  .faq-item { position: absolute; left: 0; width: 790px; }
  .faq-q {
    position: relative; padding-left: 24px;
    font-size: 21px; font-weight: 500; line-height: 26px;
  }
  .faq-q::before { content: ">"; position: absolute; left: 0; top: 0; font-weight: 400; font-size: 18px; }
  .faq-a { padding-left: 24px; margin-top: 20px; font-size: 17px; line-height: 25px; font-weight: 400; }
  .faq-a strong { font-weight: 700; }
  .hours-tab {
    position: absolute; left: 316px; top: 1000px; width: 216px; height: 40px;
    background: var(--white); border-radius: 5px 5px 0 0;
    color: var(--ink); font-size: 21px; font-weight: 500; text-align: center; line-height: 42px;
  }
  .hours-card {
    position: absolute; left: 92px; top: 1030px; width: 661px; height: 139px;
    background: var(--white); color: var(--ink);
    display: grid; grid-template-columns: 1fr 1px 1fr; align-items: center;
    padding: 0 36px 0 36px;
  }
  .hours-col { display: grid; grid-template-columns: auto 1fr; row-gap: 8px; column-gap: 12px; font-size: 17px; font-weight: 500; }
  .hours-col.right { padding-left: 24px; }
  .hours-day { white-space: nowrap; }
  .hours-divider { width: 1px; height: 90px; background: #9a9a9a; }
</style>
</head>
<body>
<main class="flyer">
  <svg class="backdrop" width="846" height="1200" viewBox="0 0 846 1200" aria-hidden="true">
    <defs>
      <linearGradient id="panelBlue" x1="0" y1="0" x2="1" y2="1">
        <stop offset="0" stop-color="#3ea6e2"/>
        <stop offset=".55" stop-color="#2b8fd4"/>
        <stop offset="1" stop-color="#1c6bb6"/>
      </linearGradient>
    </defs>
    <path d="M0 432 C 220 410 470 455 846 618 L846 1200 L0 1200 Z" fill="url(#panelBlue)"/>
  </svg>

  <div class="product-shot shot-wire-black" role="img" aria-label="Black half-rim metal spectacle frame"></div>
  <div class="product-shot shot-rimless-black" role="img" aria-label="Dark semi-rimless spectacle frame"></div>
  <div class="product-shot shot-red-metal" role="img" aria-label="Burgundy full-rim metal spectacle frame"></div>
  <div class="product-shot shot-tortoise" role="img" aria-label="Tortoiseshell acetate spectacle frame"></div>

  <svg class="question-icon" viewBox="0 0 124 124" aria-hidden="true">
    <circle cx="62" cy="62" r="62" fill="#2e9fe0"/>
    <path d="M42 36 A26 26 0 1 1 62 86" fill="none" stroke="#fff" stroke-width="11" stroke-linecap="round"/>
    <circle cx="64" cy="112" r="7" fill="#fff"/>
  </svg>

  <h1 class="faq-title">Frequently Asked Questions?</h1>

  <ol class="faq-list">
    <li class="faq-item" style="top:552px">
      <h2 class="faq-q">Can I have fashion sunglasses made to<br>my prescription?</h2>
      <p class="faq-a"><strong>Yes.</strong> It does depend on the sunglasses and your prescription.<br>We offer a range of sunglasses that can be fitted with prescription lenses.</p>
    </li>
    <li class="faq-item" style="top:693px">
      <h2 class="faq-q">If I want new prescription lenses fitted to my existing pair of glasses, do I have to go without them for a week?</h2>
      <p class="faq-a"><strong>No.</strong> We can usually fit new lenses to your own frame onsite. You only need to be without your glasses for a few hours.</p>
    </li>
    <li class="faq-item" style="top:844px">
      <h2 class="faq-q">Do I have to purchase my spectacles where my private health fund directs ?</h2>
      <p class="faq-a"><strong>No.</strong> It is your decision where to have your eyes tested and where to purchase your spectacles or contact lenses. We can direct bill your private health fund with the <strong>CLAIMPOINT</strong> system.</p>
    </li>
  </ol>

  <div class="hours-tab">Opening Hours:</div>
  <section class="hours-card" aria-label="Opening hours">
    <div class="hours-col">
      <span class="hours-day">Monday:</span><span>9.00am - 5.30pm</span>
      <span class="hours-day">Wednesday:</span><span>9.00am - 5.30pm</span>
      <span class="hours-day">Friday:</span><span>9.00am - 5.30pm</span>
    </div>
    <div class="hours-divider"></div>
    <div class="hours-col right">
      <span class="hours-day">Tuesday:</span><span>9.00am - 6.30pm</span>
      <span class="hours-day">Thursday:</span><span>9.00am - 6.30pm</span>
      <span class="hours-day">Saturday:</span><span>9.00am - 1.00pm</span>
    </div>
  </section>
</main>
</body>
</html>
```